Stationery Design Project

We need a stationery design for our Norwegian trucking company. We have existed for about 15 years and our 12 drivers uses relatively new vehicles to transport goods around in northern Norway. Long distance routes with fresh fish og food transport is our main operations.

We have already made alogo that's printed on our trucks. The logo and a picture of our trucks is attached. I think the logo i crappy, but since its already in use, changing it is not an option in this round. Still using a better colour scheme in the overall stationery and more interesting fonts is possible (altso in the logo).

Company details:
Name: Kjelvraket AS
Organisation nr 873 615 309
Post adress: 8642 Raudvik

I like minimalism and simplicity. I am avalibly for questions in normal GMT working hours either here or on mail: ivar@fjordlast.no

Reason: Hi. Im extending the deadline because I needed some time to find a vector file of our logo. Sorry for the inconvenience

Hi, and thanks for all your interest in the project. Some updates:

-          I have decided to commit to using one of the designs. Some designer will get the payment.

-          I have extended the deadline with 24 hours since I needed some time to find our firms vector logo (a slow Swedish man was holding me up)

-          We will not choose a design before the deadline. No need to rush.

-          We have received a lot of great design and think there is a need to specified the product we want to make:

o   Business Card for all our employers. I just need the design and will duplicate with the correct numbers and name myself. The information on should be: Logo, employer’s name, Phone number, email, website, Postal number and address. Use this as a template: logo, Leif Brattvoll, 47382066, Leif@fjordlast.no,, fjordlast.no, 8642 Raudvik. The order and placement of the information is your creative decision.

o   Stickers to put on the goods we travel. On the sticker the should be the following information: Logo, phone number, Tekst and link: Fraktæ av Kjelvraket. Ke du syns? Fjordlast.no/tilbakemelding (this means: Handled by Kjelvraket. What do you think Fjordlast.no/feedback -à the link will be a feedback form). The placement the information and size is your creative decision with some stings: we have been thinking of using Drukko for printing and see that a size about 6x6 cm, 8x5 or something like that. (with 3000 copies our budget is 200 punds). Any suggestions of other suppliers are welcome. Drukko price calculator http://www.drukkolabelhouse.co.uk/digital-litho-printing/printing-labels-tags/stickers/

o   Letterhead with logo, address, phone number and organizational number.

o   Envelopes with logo,address, phone number and organizational number.

Have a nice day.

 

 

• Using the blue colour in the logo and using a similar graphic approch.

```html
<!DOCTYPE html>
<html lang="no">
<head>
<meta charset="utf-8">
<title>Kjelvraket – visittkort</title>
<link rel="stylesheet" href="https://fonts.googleapis.com/css2?family=Open+Sans:wght@400;600;700&display=swap">
<style>
  :root {
    --backdrop: #9a9da2;
    --white: #ffffff;
    --navy: #0b4a9e;
    --royal: #0672bb;
    --stripe: #2f86cf;
    --ink: #2b2b2b;
    --card-line: #6b6e73;
  }
  * { margin: 0; padding: 0; box-sizing: border-box; }
  html, body { width: 1200px; height: 751px; overflow: hidden; }
  body {
    background: var(--backdrop);
    font-family: "Open Sans", Arial, sans-serif;
    position: relative;
  }
  .card {
    position: absolute;
    width: 525px;
    height: 299px;
    border-radius: 24px;
    overflow: hidden;
    text-align: center;
  }
  .card--front { left: 50px; top: 55px; background: var(--white); }
  .card--back-white { left: 620px; top: 50px; background: var(--white); border: 1px solid var(--card-line); }
  .card--back-navy { left: 50px; top: 388px; background: var(--navy); }
  .card--back-royal { left: 620px; top: 388px; background: var(--royal); }

  .wave { position: absolute; left: 0; top: 0; width: 525px; height: 299px; }

  .brand {
    position: absolute;
    left: 0; right: 0;
    display: flex;
    align-items: center;
    justify-content: center;
    gap: 14px;
    font-weight: 700;
    font-size: 50px;
    letter-spacing: -0.5px;
    line-height: 1;
  }
  .brand__dot { width: 22px; height: 22px; border-radius: 50%; background: currentColor; }
  .card--front .brand { top: 70px; color: var(--navy); }
  .card--back-white .brand { top: 128px; color: var(--navy); }
  .card--back-navy .brand, .card--back-royal .brand { top: 128px; color: var(--white); }

  .holder {
    position: absolute; left: 0; right: 0; top: 174px;
    font-size: 21px; font-weight: 700; color: var(--navy);
  }
  .contact {
    position: absolute; left: 0; right: 0;
    color: var(--white); font-size: 15px;
    display: flex; justify-content: center; gap: 12px;
  }
  .contact--row1 { top: 238px; }
  .contact--row2 { top: 263px; }
  .contact__item { display: inline-flex; align-items: center; gap: 5px; }
  .contact__item svg { width: 11px; height: 11px; fill: var(--white); }

  .site {
    position: absolute; left: 0; right: 0; top: 248px;
    font-size: 17px; letter-spacing: 3.5px;
  }
  .card--back-white .site { color: var(--ink); }
  .card--back-navy .site, .card--back-royal .site { color: var(--white); }
</style>
</head>
<body>

<section class="card card--front">
  <svg class="wave" viewBox="0 0 525 299" aria-hidden="true">
    <path d="M0 164 Q262 250 525 158 L525 299 L0 299 Z" fill="var(--stripe)"/>
    <path d="M0 174 Q262 262 525 170 L525 299 L0 299 Z" fill="var(--navy)"/>
  </svg>
  <div class="brand"><span class="brand__dot"></span>Kjelvraket</div>
  <p class="holder">Leif Brattvoll</p>
  <div class="contact contact--row1">
    <span class="contact__item">
      <svg viewBox="0 0 12 12"><path d="M2 1 L4.5 1 L5.5 3.5 L4 4.8 Q5 7 7.2 8 L8.5 6.5 L11 7.5 L11 10 Q6 11 3 8 Q0.5 5 2 1 Z"/></svg>47382066
    </span>
    <span class="contact__item">Org nr 873 615 309</span>
  </div>
  <div class="contact contact--row2">
    <span class="contact__item">
      <svg viewBox="0 0 12 12"><path d="M1 3 L6 6.5 L11 3 L11 10 L1 10 Z M1.5 2 L10.5 2 L6 5.2 Z"/></svg>Leif@fjordlast.no
    </span>
    <span class="contact__item">
      <svg viewBox="0 0 12 12"><circle cx="6" cy="6" r="5" fill="none" stroke="#fff" stroke-width="1.3"/><path d="M1 6 H11 M6 1 V11" stroke="#fff" stroke-width="1"/></svg>www.fjordlast.no
    </span>
    <span class="contact__item">
      <svg viewBox="0 0 12 12"><path d="M6 1 L11.5 6 L10 6 L10 11 L2 11 L2 6 L0.5 6 Z"/></svg>8642 Raudvik
    </span>
  </div>
</section>

<section class="card card--back-white">
  <div class="brand"><span class="brand__dot"></span>Kjelvraket</div>
  <p class="site">www.fjordlast.no</p>
</section>

<section class="card card--back-navy">
  <div class="brand"><span class="brand__dot"></span>Kjelvraket</div>
  <p class="site">www.fjordlast.no</p>
</section>

<section class="card card--back-royal">
  <div class="brand"><span class="brand__dot"></span>Kjelvraket</div>
  <p class="site">www.fjordlast.no</p>
</section>

</body>
</html>
```